KLV Plant Services

We are a heavy diesel mechanical business with additional air con certificates, remapping engine rebuilt

Contact Information for Business Card

Company Name, Director Name, Managing Director, Contact details, email and website

Font styles to use
Serif
Script

```html
<!DOCTYPE html>
<html lang="en">
<head>
<meta charset="utf-8">
<title>KLV Plant Services – Business Card</title>
<link href="https://fonts.googleapis.com/css2?family=Roboto:wght@400;700;900&display=swap" rel="stylesheet">
<style>
  :root {
    --navy: #2f2c80;
    --ink: #1b1b1b;
    --paper: #ffffff;
    --stage: #6c6f70;
    --muted: #222;
  }
  * { box-sizing: border-box; margin: 0; padding: 0; }
  html, body { width: 1200px; height: 780px; overflow: hidden; }
  body {
    background: var(--stage);
    font-family: "Roboto", Arial, sans-serif;
    position: relative;
  }
  .card {
    position: absolute;
    width: 520px;
    height: 298px;
    border-radius: 18px;
    overflow: hidden;
    box-shadow: 0 10px 24px rgba(0,0,0,.35);
  }
  .card--back {
    left: 50px; top: 120px;
    background: var(--navy);
    display: flex; align-items: center; justify-content: center;
  }
  .card--back .brand-name {
    color: var(--paper);
    font-weight: 900;
    font-size: 42px;
    letter-spacing: .5px;
    display: flex; align-items: center; gap: 14px;
  }
  .brand-dot {
    width: 16px; height: 16px; border-radius: 50%;
    background: currentColor;
  }
  .card--front {
    left: 630px; top: 362px;
    background: var(--paper);
  }
  .front-band { position: absolute; inset: 0; }
  .front-brand {
    position: absolute; left: 30px; top: 30px;
    color: var(--navy); font-weight: 900; font-size: 22px;
    display: flex; align-items: center; gap: 8px;
  }
  .front-brand .brand-dot { width: 10px; height: 10px; }
  .person {
    position: absolute; left: 34px; top: 96px;
    padding-left: 14px;
    border-left: 10px solid var(--ink);
  }
  .person__name {
    color: var(--navy); font-weight: 700; font-size: 21px; letter-spacing: .4px;
  }
  .person__title { color: var(--ink); font-weight: 700; font-size: 12px; margin-top: 2px; }
  .address {
    position: absolute; left: 58px; top: 154px;
    font-size: 14px; line-height: 17px; color: var(--muted);
  }
  .contacts {
    position: absolute; left: 58px; top: 200px;
    list-style: none; font-size: 14px; line-height: 18px; color: var(--muted);
  }
  .contacts li { display: flex; align-items: center; gap: 7px; }
  .contacts svg { width: 11px; height: 11px; fill: var(--navy); flex: none; }
</style>
</head>
<body>
  <section class="card card--back" aria-label="Card back">
    <div class="brand-name"><span class="brand-dot"></span>KLV Plant Services</div>
  </section>

  <section class="card card--front" aria-label="Card front">
    <svg class="front-band" viewBox="0 0 520 298" preserveAspectRatio="none" aria-hidden="true">
      <polygon points="0,284 300,284 318,266 520,266 520,298 0,298" fill="var(--navy)"/>
      <polygon points="300,284 318,266 520,266 520,262 316,262 296,284" fill="var(--ink)"/>
      <polygon points="510,130 520,130 520,266 510,266" fill="var(--navy)"/>
    </svg>
    <div class="front-brand"><span class="brand-dot"></span>KLV Plant Services</div>
    <div class="person">
      <div class="person__name">MARK ELSTON</div>
      <div class="person__title">Managing Director</div>
    </div>
    <address class="address" style="font-style:normal">
      418 C Harlow St<br>Nashville, TN 37206
    </address>
    <ul class="contacts">
      <li><svg viewBox="0 0 12 12"><path d="M2 1h3l1 3-2 1a7 7 0 0 0 3 3l1-2 3 1v3c-6 0-9-3-9-9z"/></svg>(615) 555-0148</li>
      <li><svg viewBox="0 0 12 12"><path d="M0 2h12v8H0z M0 2l6 5 6-5" fill="none" stroke="var(--navy)" stroke-width="1.4"/></svg>klvplantservices@gmail.com</li>
      <li><svg viewBox="0 0 12 12"><circle cx="6" cy="6" r="6"/></svg>www.klvplantservices.com</li>
    </ul>
  </section>
</body>
</html>
```